BOLD & MINIMALIST DESIGN NEEDED

We want a very bold but minimalistic business card design that is impactful and utilizes both sides of the business card. Our current logo is included for your use.

We want bold fonts and good use of negative space. We don't want the logo to overpower the design.

Target Market(s)

Professionals who are building new commercial buildings.

Industry/Entity Type

Construction

Contact Information for Business Card

Name, Title, email, office phone, cell phone, website

Font styles to use
Serif
Sans Serif

Requirements
Must have
• Bold design!

```html
<!DOCTYPE html>
<html lang="en">
<head>
<meta charset="utf-8">
<title>Ridgeline Design + Build — Business Card</title>
<link href="https://fonts.googleapis.com/css2?family=Montserrat:wght@400;500;800&display=swap" rel="stylesheet">
<style>
  :root {
    --stage: #3b3b3b;
    --paper: #ffffff;
    --ink: #111111;
    --green: #5e9a2e;
    --green-bright: #7cc242;
    --grey: #6d6d6d;
    --back-dark: #141414;
    --back-mid: #2b2b2b;
  }
  * { box-sizing: border-box; margin: 0; padding: 0; }
  html, body { width: 1200px; height: 791px; overflow: hidden; }
  body {
    background: var(--stage);
    font-family: "Montserrat", sans-serif;
    position: relative;
  }
  .card {
    position: absolute;
    top: 247px;
    width: 520px;
    height: 297px;
    border-bottom: 3px solid var(--green);
    box-shadow: 0 14px 30px rgba(0,0,0,.35);
  }
  .card--front { left: 50px; background: var(--paper); }
  .card--back { left: 630px; background: var(--back-dark); overflow: hidden; }

  .brand {
    position: absolute;
    left: 36px;
    top: 120px;
    width: 200px;
    display: flex;
    align-items: center;
    gap: 10px;
  }
  .brand__mark { width: 14px; height: 14px; background: var(--green-bright); flex: none; }
  .brand__name {
    font-weight: 800;
    font-size: 17px;
    line-height: 1.15;
    letter-spacing: .5px;
    color: var(--ink);
    text-transform: uppercase;
  }
  .divider {
    position: absolute;
    left: 262px;
    top: 90px;
    width: 1px;
    height: 117px;
    background: var(--green);
  }
  .contact { position: absolute; left: 288px; top: 62px; }
  .contact__name {
    font-weight: 800;
    font-size: 17px;
    color: var(--green);
    text-transform: uppercase;
    letter-spacing: .3px;
  }
  .contact__title { font-size: 12px; color: var(--grey); margin-top: 2px; }
  .contact__list { list-style: none; margin-top: 26px; }
  .contact__item {
    display: flex;
    align-items: center;
    gap: 8px;
    font-size: 12.5px;
    color: var(--grey);
    line-height: 1.55;
  }
  .contact__item svg { width: 11px; height: 11px; flex: none; }

  .back__pattern {
    position: absolute;
    inset: 0;
    background: linear-gradient(120deg, var(--back-dark) 0%, var(--back-mid) 60%, #3a3a3a 100%);
  }
  .back__brand {
    position: absolute;
    right: 48px;
    top: 150px;
    display: flex;
    align-items: center;
    gap: 8px;
  }
  .back__brand .brand__mark { width: 10px; height: 10px; }
  .back__brand .brand__name { color: var(--paper); font-size: 13px; }
</style>
</head>
<body>
  <section class="card card--front">
    <div class="brand">
      <span class="brand__mark"></span>
      <span class="brand__name">Ridgeline<br>Design + Build</span>
    </div>
    <div class="divider"></div>
    <div class="contact">
      <p class="contact__name">Marcus Dalton</p>
      <p class="contact__title">President</p>
      <ul class="contact__list">
        <li class="contact__item">
          <svg viewBox="0 0 12 12"><path d="M2 1h3l1 3-2 1a7 7 0 0 0 3 3l1-2 3 1v3c-6 0-9-3-9-9z" fill="var(--green)"/></svg>
          555-014-2200
        </li>
        <li class="contact__item">
          <svg viewBox="0 0 12 12"><rect x="3" y="1" width="6" height="10" rx="1" fill="none" stroke="var(--grey)" stroke-width="1.2"/></svg>
          555-014-2200
        </li>
        <li class="contact__item">
          <svg viewBox="0 0 12 12"><rect x="1" y="3" width="10" height="7" fill="var(--green)"/><path d="M1 3l5 4 5-4" fill="none" stroke="#fff" stroke-width="1"/></svg>
          m.dalton@rdb-build.com
        </li>
        <li class="contact__item">
          <svg viewBox="0 0 12 12"><circle cx="6" cy="6" r="5" fill="var(--green)"/><path d="M1 6h10M6 1c-3 3-3 7 0 10M6 1c3 3 3 7 0 10" fill="none" stroke="#fff" stroke-width=".8"/></svg>
          www.rdb-build.com
        </li>
      </ul>
    </div>
  </section>

  <section class="card card--back">
    <div class="back__pattern" role="img" aria-label="Repeating embossed brand-mark pattern in black and dark grey"></div>
    <div class="back__brand">
      <span class="brand__mark"></span>
      <span class="brand__name">Ridgeline</span>
    </div>
  </section>
</body>
</html>
```